velorimo.gr wordpress makeover

We need a makeover of our wordpress website velorimo.gr We are a company that provides astrology services via phone either by billable phone number or by prepaid packages.This is what we sell. Moreover, we share everyday astrology related articles to our blog. It will be a multy page website. Our goal is always to sell our phone prepaid packages or to make the visitor of the website call our billable numbers. Our website should have:
-a home page introducing its content (astrologers, call packages, blog section with categories).
-astrologers page (you can see the existing one to understand)
-Phone packages page (eshop page where you can buy prepaid phone packages. woo commerce maybe)
- Blog page divined by categories.
The website should have places for display banners eg. a sidebar.
I will provide some screen shots of websites we like. You can always visit our existing website www.velorimo.gr to see it for yourself.

Target Market(s)

people seeking for future telling - astrologer services via phone. People who like to be informed about everyday astrology predictions

Industry/Entity Type

Astrology - tarot services via phone

Coding

Coded - Design and coding required

Number of Pages Required

5+ page

Font styles to use
Decorative
Script

Colors
6B429C
8869AF
B7A5CE
E3DAEB
F3F0F8

Requirements
Must have
• -Home page -Astrologers page -Phone packages page (eshop) -Blog page with categories - Made following the guidelines of quenbly so as to be efficient in quenbly ads marketing. Mobile friendly.
Nice to have
• Nice call to action buttons to call or buy packages. Sidebar with banner ads of maybe our offers.

```html
<!DOCTYPE html>
<html lang="el">
<head>
<meta charset="utf-8">
<title>velorimo – αστρολόγοι μέσω τηλεφώνου</title>
<link rel="stylesheet" href="https://fonts.googleapis.com/css2?family=Manrope:wght@300;500;700;800&family=Open+Sans:ital,wght@0,400;0,600;1,400;1,700&display=swap">
<style>
:root{
  --violet:#6B429C;
  --violet-deep:#4a2a85;
  --violet-dark:#3a1f70;
  --lilac:#8869AF;
  --lavender:#B7A5CE;
  --mist:#E3DAEB;
  --pale:#F3F0F8;
  --light-bg:#d9d9e3;
  --ink:#2a2a33;
  --muted:#555060;
  --white:#ffffff;
}
*{box-sizing:border-box;margin:0;padding:0}
html,body{width:1200px;height:3667px;overflow:hidden}
body{position:relative;font-family:"Open Sans",sans-serif;color:var(--ink);background:var(--light-bg)}
.abs{position:absolute}
h1,h2,h3,.heading{font-family:"Manrope",sans-serif}

/* header + hero */
.hero{left:0;top:0;width:1200px;height:770px;background:radial-gradient(circle at 70% 40%,#8a4fcf 0%,#5a2fa0 40%,#3d1f7a 80%)}
.logo{font-family:"Manrope",sans-serif;font-weight:300;color:var(--white);letter-spacing:1px}
.header-logo{left:111px;top:42px;font-size:40px}
.nav{top:56px;display:flex;gap:0;font-family:"Manrope",sans-serif;font-weight:700;font-size:16px;color:var(--white)}
.nav a{color:inherit;text-decoration:none;position:absolute;white-space:nowrap}
.call-pill{display:flex;align-items:center;gap:10px;background:var(--white);border-radius:30px;padding:4px 14px 4px 5px;color:var(--violet);font-family:"Manrope",sans-serif;font-weight:800;line-height:1.05}
.call-pill .ico{width:36px;height:36px;border-radius:50%;border:2px solid var(--violet);display:flex;align-items:center;justify-content:center}
.call-pill small{display:block;font-size:12px;font-weight:500;font-style:italic}
.call-pill b{font-size:15px}
.header-call{left:925px;top:44px;width:161px;height:46px}
.hero-title{left:113px;top:252px;font-size:45px;font-weight:800;color:var(--white);line-height:68px}
.hero-text{left:113px;top:398px;width:430px;font-size:15px;font-style:italic;color:var(--white);line-height:23px}
.hero-call{left:114px;top:502px;width:161px;height:46px}
.zodiac-wheel{left:593px;top:84px;width:590px;height:590px;border-radius:50%;background:radial-gradient(circle,#c07cf0 0%,#7a4ad0 35%,rgba(110,70,200,.35) 70%,rgba(90,50,170,0) 100%);border:2px solid rgba(220,200,255,.6)}

/* astrologers */
.section-title{width:1200px;text-align:center;font-size:40px;font-weight:800;color:var(--ink)}
.astro-card{top:937px;width:481px;height:552px;background:var(--white);border-radius:6px;box-shadow:0 4px 14px rgba(60,40,90,.15)}
.astro-photo{left:6px;top:6px;width:469px;height:339px;background:linear-gradient(135deg,#2d1a5a,#5b3aa8 60%,#3b2a7a)}
.astro-name{left:278px;top:108px;font-family:"Manrope",sans-serif;font-weight:800;font-size:26px;color:var(--white);line-height:32px}
.astro-role{left:278px;top:194px;border:2px solid var(--white);border-radius:22px;padding:4px 14px;font-family:"Manrope",sans-serif;font-weight:700;font-size:20px;color:var(--white);background:rgba(107,66,156,.6)}
.contact-pill{top:318px;height:44px;display:flex;align-items:center;gap:12px;background:var(--white);border-radius:24px;padding:0 18px 0 5px;box-shadow:0 2px 8px rgba(0,0,0,.2);font-family:"Manrope",sans-serif;font-weight:800;font-size:32px;color:var(--violet)}
.contact-pill .ico{width:36px;height:36px;border-radius:50%;background:var(--violet);display:flex;align-items:center;justify-content:center}
.astro-desc{left:26px;top:402px;width:430px;font-size:13px;font-style:italic;line-height:21px;color:var(--muted)}
.astro-link{left:25px;top:494px;font-family:"Manrope",sans-serif;font-weight:700;font-size:16px;color:var(--violet);text-decoration:underline}
.slider-arrow{width:22px;height:22px;border-radius:50%;background:#4a4a52;display:flex;align-items:center;justify-content:center}

/* packages */
.packages{left:0;top:1608px;width:1200px;height:712px;background:var(--violet-deep)}
.package{top:211px;width:314px;height:341px;border:2px solid var(--white);border-radius:16px;text-align:center;color:var(--white)}
.package.featured{background:var(--white);color:var(--ink)}
.package h3{margin-top:58px;font-size:28px;font-weight:800;line-height:40px}
.package .price{margin-top:12px;font-family:"Manrope",sans-serif;font-size:44px;font-weight:800;font-style:italic}
.package.featured .price{color:var(--violet)}
.package p{margin:20px auto 0;width:260px;font-size:13px;font-weight:700;font-style:italic;line-height:22px}

/* blog */
.blog-image{background:linear-gradient(120deg,#c96b2a,#7a3a1e 50%,#2a1a3a)}
.blog-image.alt{background:radial-gradient(circle at 50% 45%,#6fb6ff,#1f4aa8 35%,#0a1535 75%)}
.blog-card{background:var(--white);box-shadow:0 4px 14px rgba(60,40,90,.18)}
.date-badge{width:57px;height:50px;background:var(--violet-deep);color:var(--white);text-align:center;font-family:"Manrope",sans-serif;line-height:1.1;padding-top:5px}
.date-badge small{display:block;font-size:13px}
.date-badge b{font-size:19px}
.blog-rule{width:2px;background:var(--violet)}
.blog-card h3{font-size:20px;font-weight:800;line-height:24px;color:var(--ink)}
.blog-card p{font-size:13px;line-height:19px;color:var(--muted);font-family:Arial,sans-serif}
.blog-nav{width:22px;height:22px;border-radius:50%;background:var(--violet-deep);display:flex;align-items:center;justify-content:center}

/* footer */
.footer{left:0;top:3240px;width:1200px;height:427px;background:linear-gradient(#5a3595,#6d4aa6 60%,#8a6ab8)}
.footer-logo{width:1200px;text-align:center;top:128px;font-size:42px;font-weight:800}
.footer-nav{top:188px;width:1200px;display:flex;justify-content:center;gap:64px;font-size:17px;font-style:italic;color:var(--white)}
.copyright{top:228px;width:1200px;text-align:center;font-size:11px;font-style:italic;color:var(--white)}
.footer-rule{left:112px;top:265px;width:976px;height:1px;background:rgba(255,255,255,.7)}
.social{top:290px;width:14px;height:14px;border-radius:50%;background:var(--white)}
.footer-call{left:517px;top:339px;width:166px;height:51px;border-radius:30px;border:2px solid var(--white);background:var(--violet);display:flex;align-items:center;gap:10px;padding-left:5px;color:var(--white);font-family:"Manrope",sans-serif;font-weight:800;font-size:30px}
.footer-call .ico{width:38px;height:38px;border-radius:50%;border:2px solid var(--white);display:flex;align-items:center;justify-content:center}
</style>
</head>
<body>

<svg width="0" height="0" style="position:absolute">
  <defs>
    <symbol id="phone" viewBox="0 0 24 24"><path d="M6.6 10.8a15.1 15.1 0 0 0 6.6 6.6l2.2-2.2a1 1 0 0 1 1-.25 11.4 11.4 0 0 0 3.6.57 1 1 0 0 1 1 1V20a1 1 0 0 1-1 1A17 17 0 0 1 3 4a1 1 0 0 1 1-1h3.5a1 1 0 0 1 1 1c0 1.25.2 2.45.57 3.57a1 1 0 0 1-.25 1z" fill="currentColor"/></symbol>
    <symbol id="mail" viewBox="0 0 24 24"><path d="M3 5h18v14H3z M3 5l9 7 9-7" fill="none" stroke="currentColor" stroke-width="2" stroke-linejoin="round"/></symbol>
  </defs>
</svg>

<!-- hero -->
<section class="abs hero">
  <div class="abs logo header-logo">velorimo</div>
  <nav class="abs nav" style="left:0;width:1200px">
    <a style="left:495px">αστρολόγοι</a>
    <a style="left:644px">πακέτα κλήσεων</a>
    <a style="left:846px">Blog</a>
  </nav>
  <a class="abs call-pill header-call"><span class="ico"><svg width="18" height="18" style="color:var(--violet)"><use href="#phone"/></svg></span><span><small>κάλεσε τώρα</small><b>18820</b></span></a>
  <div class="abs zodiac-wheel" role="img" aria-label="Illustrated zodiac wheel with the twelve signs"></div>
  <h1 class="abs hero-title">Καλωσόρισες στο<br>Τα ζώδια για σήμερα</h1>
  <p class="abs hero-text">Το τυπικό κομμάτι του Lorem Ipsum που χρησιμοποιήθηκε από το 1500 αναπαράγεται παρακάτω για όσους ενδιαφέρονται.</p>
  <a class="abs call-pill hero-call"><span class="ico"><svg width="18" height="18" style="color:var(--violet)"><use href="#phone"/></svg></span><span><small>κάλεσε τώρα</small><b>18820</b></span></a>
</section>
<svg class="abs" style="left:0;top:700px" width="1200" height="80" viewBox="0 0 1200 80" preserveAspectRatio="none"><polygon fill="var(--light-bg)" points="0,40 40,22 80,38 130,14 170,30 220,10 260,34 310,18 360,36 400,20 450,32 500,8 540,28 590,16 640,34 690,12 740,30 790,18 840,36 890,14 940,28 990,10 1040,32 1090,20 1140,36 1200,16 1200,80 0,80"/></svg>

<!-- astrologers -->
<h2 class="abs section-title" style="left:0;top:840px">Οι αστρολόγοι μας</h2>
<div class="abs slider-arrow" style="left:54px;top:1174px"><svg width="12" height="12" viewBox="0 0 12 12"><path d="M10 6H2M5 3L2 6l3 3" stroke="#fff" stroke-width="1.6" fill="none"/></svg></div>
<div class="abs slider-arrow" style="left:1096px;top:1174px"><svg width="12" height="12" viewBox="0 0 12 12"><path d="M2 6h8M7 3l3 3-3 3" stroke="#fff" stroke-width="1.6" fill="none"/></svg></div>

<article class="abs astro-card" style="left:94px">
  <div class="abs astro-photo" role="img" aria-label="Portrait photo of the astrologer over a starry zodiac background"></div>
  <div class="abs astro-name">Ελένη<br>Σταυράκη</div>
  <div class="abs astro-role">Αστρολόγος</div>
  <div class="abs contact-pill" style="left:42px"><span class="ico"><svg width="18" height="18" style="color:#fff"><use href="#phone"/></svg></span>18820</div>
  <div class="abs contact-pill" style="left:252px"><span class="ico"><svg width="18" height="18" style="color:#fff"><use href="#mail"/></svg></span>18820</div>
  <p class="abs astro-desc">Αστρολόγος με εξειδίκευση στην Αστροψυχολογία, με πολλά χρόνια έρευνας πάνω στις ανθρώπινες σχέσεις. Κάλεσε τώρα για μια προσωπική αστρολογική πρόβλεψη. Έχω τις απαντήσεις στα ερωτήματα που σε απασχολούν.</p>
  <a class="abs astro-link">Επικοινώνησε τώρα</a>
</article>

<article class="abs astro-card" style="left:598px">
  <div class="abs astro-photo" role="img" aria-label="Portrait photo of the astrologer over a blue zodiac background" style="background:linear-gradient(135deg,#5a5ad0,#6b42c0 60%,#4a3aa0)"></div>
  <div class="abs astro-name">Ελένη<br>Σταυράκη</div>
  <div class="abs astro-role">Αστρολόγος</div>
  <div class="abs contact-pill" style="left:42px"><span class="ico"><svg width="18" height="18" style="color:#fff"><use href="#phone"/></svg></span>18820</div>
  <div class="abs contact-pill" style="left:252px"><span class="ico"><svg width="18" height="18" style="color:#fff"><use href="#mail"/></svg></span>18820</div>
  <p class="abs astro-desc">Αστρολόγος με εξειδίκευση στην Αστροψυχολογία, με πολλά χρόνια έρευνας πάνω στις ανθρώπινες σχέσεις. Κάλεσε τώρα για μια προσωπική αστρολογική πρόβλεψη. Έχω τις απαντήσεις στα ερωτήματα που σε απασχολούν.</p>
  <a class="abs astro-link">Επικοινώνησε τώρα</a>
</article>

<!-- packages -->
<section class="abs packages">
  <h2 class="abs section-title" style="left:0;top:106px;color:var(--white)">τηλεφωνικά πακέτα</h2>
  <div class="abs package" style="left:112px"><h3>20 λεπτά χρόνο<br>ομιλίας</h3><div class="price">30€</div><p>Το Lorem Ipsum είναι απλώς εικονικό κείμενο της βιομηχανίας εκτύπωσης και</p></div>
  <div class="abs package featured" style="left:443px"><h3>40 λεπτά χρόνο<br>ομιλίας</h3><div class="price">70€</div><p>Το Lorem Ipsum είναι απλώς εικονικό κείμενο της βιομηχανίας εκτύπωσης και</p></div>
  <div class="abs package" style="left:773px"><h3>80 λεπτά χρόνο<br>ομιλίας</h3><div class="price">120€</div><p>Το Lorem Ipsum είναι απλώς εικονικό κείμενο της βιομηχανίας εκτύπωσης και</p></div>
</section>
<svg class="abs" style="left:0;top:1580px" width="1200" height="40" viewBox="0 0 1200 40" preserveAspectRatio="none"><polygon fill="var(--violet-deep)" points="0,12 50,24 100,8 150,22 200,6 250,20 300,10 350,26 400,8 450,20 500,4 550,22 600,10 650,24 700,6 750,20 800,12 850,26 900,8 950,22 1000,6 1050,20 1100,10 1150,24 1200,8 1200,40 0,40"/></svg>

<!-- blog -->
<h2 class="abs section-title" style="left:0;top:2400px">τηλεφωνικά πακέτα</h2>

<div class="abs blog-image" style="left:176px;top:2511px;width:466px;height:232px" role="img" aria-label="Photo of a hand laying tarot cards beside candles and crystals"></div>
<article class="abs blog-card" style="left:622px;top:2534px;width:410px;height:239px">
  <div class="abs blog-rule" style="left:60px;top:40px;height:199px"></div>
  <div class="abs" style="left:115px;top:38px;width:270px"><h3>Το Lorem Ipsum είναι απλώς εικονικό</h3></div>
  <p class="abs" style="left:115px;top:116px;width:270px">Το Lorem Ipsum είναι απλώς εικονικό κείμενο της βιομηχανίας εκτύπωσης και στοιχειοθεσίας. Το Lorem Ipsum ήταν το τυπικό εικονικό κείμενο της βιομηχανίας από το 1500, όταν ένας άγνωστος</p>
</article>
<div class="abs date-badge" style="left:655px;top:2530px"><small>22</small><b>Ιαν</b></div>

<div class="abs blog-image alt" style="left:567px;top:2848px;width:465px;height:234px" role="img" aria-label="Photo of hands holding a glowing zodiac globe"></div>
<article class="abs blog-card" style="left:176px;top:2878px;width:410px;height:234px">
  <div class="abs blog-rule" style="left:60px;top:38px;height:196px"></div>
  <div class="abs" style="left:119px;top:32px;width:260px"><h3>Το Lorem Ipsum είναι απλώς εικονικό</h3></div>
  <p class="abs" style="left:119px;top:108px;width:260px">Το Lorem Ipsum είναι απλώς εικονικό κείμενο της βιομηχανίας εκτύπωσης και στοιχειοθεσίας. Το Lorem Ipsum ήταν το τυπικό εικονικό κείμενο της βιομηχανίας από το 1500, όταν ένας άγνωστος</p>
</article>
<div class="abs date-badge" style="left:209px;top:2866px"><small>22</small><b>Ιαν</b></div>

<div class="abs blog-nav" style="left:574px;top:3173px"><svg width="10" height="10" viewBox="0 0 10 10"><path d="M6.5 1.5L3 5l3.5 3.5" stroke="#fff" stroke-width="1.8" fill="none"/></svg></div>
<div class="abs blog-nav" style="left:604px;top:3173px"><svg width="10" height="10" viewBox="0 0 10 10"><path d="M3.5 1.5L7 5 3.5 8.5" stroke="#fff" stroke-width="1.8" fill="none"/></svg></div>

<!-- footer -->
<footer class="abs footer">
  <div class="abs logo footer-logo" style="left:0">velorimo</div>
  <nav class="abs footer-nav" style="left:0"><span>αστρολόγοι</span><span>πακέτα κλήσεων</span><span>Τελευταίο Blog</span><span>Επικοινωνήστε μαζί μας</span></nav>
  <p class="abs copyright" style="left:0">© Copyright 2022 velorimo.gr | Όλα τα δικαιώματα διατηρούνται.</p>
  <div class="abs footer-rule"></div>
  <span class="abs social" style="left:593px"></span>
  <span class="abs social" style="left:619px"></span>
  <span class="abs social" style="left:645px"></span>
  <a class="abs footer-call"><span class="ico"><svg width="20" height="20" style="color:#fff"><use href="#phone"/></svg></span>18820</a>
</footer>
<svg class="abs" style="left:0;top:3220px" width="1200" height="40" viewBox="0 0 1200 40" preserveAspectRatio="none"><polygon fill="#5a3595" points="0,24 40,10 90,26 140,6 190,22 240,12 290,28 340,8 390,20 440,4 490,24 540,12 590,28 640,6 690,22 740,10 790,26 840,8 890,20 940,4 990,22 1040,12 1090,28 1140,8 1200,20 1200,40 0,40"/></svg>

</body>
</html>
```